Business Card Re-Design/Update

We'd like to update out business cards. I've included our current "Style guide" which has the colour scheme of the organisation in it. I've also included the branding files with logos etc in them.

I've also included a copy of one of our existing cards so that you can see how ugly/dated they look. I'd like a fresh modern corporate look.

Target Market(s)

These are for our clients, potential clients, industry contacts - like all business cards

Contact Information for Business Card

Name
Position
Company Address - Level 1, 47 Fernby Street, Carlow Qld 4072
Direct Phone
mobile
Email
Website -www.korvalit.com.au
Logo

Colors

Designer to choose colors to be used in the design.

Requirements
Must have
• Main Logo
• Cards will need to be editable to be able to personalize them for each new employee.
Nice to have
• The MapOut, ShipWell, KeepSteady would be okay to have if they can be sensibly and professionally added to the look without detracting from the main imagery.
• Maybe they could go on the back of the card? will leave this to your creative discretion as to whether/where they fit.
Should not have
• Should not have decorative or script fonts

```html
<!DOCTYPE html>
<html lang="en">
<head>
<meta charset="utf-8">
<title>korvalIT business card</title>
<link rel="stylesheet" href="https://fonts.googleapis.com/css2?family=Roboto:wght@400;500;700&display=swap">
<style>
  :root {
    --bg: #e9e7e4;
    --paper: #f7f7f6;
    --red: #d81b22;
    --red-dark: #b8121a;
    --ink: #222222;
    --white: #ffffff;
    --green: #6aa842;
    --blue: #2a8fd6;
    --magenta: #c42a8e;
    --rule: #9a9a9a;
  }
  html, body {
    margin: 0;
    width: 1200px;
    height: 911px;
    overflow: hidden;
    background: var(--bg);
    font-family: "Roboto", Arial, sans-serif;
  }
  .canvas { position: relative; width: 1200px; height: 911px; }
  .card {
    position: absolute;
    background: var(--paper);
    box-shadow: 0 10px 28px rgba(0,0,0,0.18);
    overflow: hidden;
  }
  .card-front { left: 150px; top: 175px; width: 340px; height: 560px; }
  .card-back { left: 540px; top: 285px; width: 560px; height: 340px; }
  .front-band { position: absolute; inset: 0; }
  .brand {
    position: absolute;
    display: flex;
    align-items: center;
    gap: 8px;
    font-weight: 700;
    color: var(--ink);
    letter-spacing: 0.2px;
  }
  .brand-square { background: var(--red); flex: none; }
  .card-front .brand { left: 0; right: 0; top: 95px; justify-content: center; font-size: 30px; }
  .card-front .brand-square { width: 22px; height: 22px; }
  .contact {
    position: absolute;
    left: 0; right: 0; top: 282px;
    text-align: center;
    color: var(--white);
    font-size: 13.5px;
    line-height: 1.32;
  }
  .contact-name { font-weight: 700; font-size: 18px; letter-spacing: 0.5px; margin: 0; }
  .contact-role { margin: 0 0 8px; font-size: 13.5px; }
  .contact-rule { width: 46px; height: 1px; background: rgba(255,255,255,0.8); margin: 8px auto; border: 0; }
  .contact p { margin: 0; }
  .contact-label { font-weight: 500; }
  .card-back .brand { left: 0; right: 0; top: 135px; justify-content: center; font-size: 40px; color: var(--red); }
  .card-back .brand-square { width: 30px; height: 30px; }
  .services {
    position: absolute;
    left: 0; right: 0; bottom: 34px;
    display: flex;
    justify-content: center;
    align-items: center;
    gap: 14px;
    font-size: 21px;
    font-weight: 500;
  }
  .service-sep { width: 1px; height: 20px; background: var(--rule); }
  .service-map { color: var(--green); }
  .service-ship { color: var(--blue); }
  .service-keep { color: var(--magenta); }
</style>
</head>
<body>
<main class="canvas">
  <section class="card card-front" aria-label="Card front">
    <svg class="front-band" width="340" height="560" viewBox="0 0 340 560" aria-hidden="true">
      <defs>
        <linearGradient id="redFill" x1="0" y1="0" x2="0" y2="1">
          <stop offset="0" stop-color="#e02128"/>
          <stop offset="1" stop-color="#b8121a"/>
        </linearGradient>
      </defs>
      <polygon points="0,70 140,230 340,180 340,560 0,560" fill="url(#redFill)"/>
    </svg>
    <div class="brand"><span class="brand-square"></span><span>korvalIT</span></div>
    <div class="contact">
      <p class="contact-name">MAREN HOLT</p>
      <p class="contact-role">Business Development Manager</p>
      <p>Level 1, 47 Fernby Street</p>
      <p>Carlow Qld 4072</p>
      <hr class="contact-rule">
      <p><span class="contact-label">P :</span> +61 (0)7 3480 2210</p>
      <p><span class="contact-label">P :</span> +61 (0)7 3480 2217</p>
      <p><span class="contact-label">C :</span> +61 (0)412 506 938</p>
      <p><span class="contact-label">F :</span> +61 (0)7 3480 2299</p>
      <hr class="contact-rule">
      <p>mholt@korvalit.com.au</p>
      <p>www.korvalit.com.au</p>
    </div>
  </section>

  <section class="card card-back" aria-label="Card back">
    <div class="brand"><span class="brand-square"></span><span>korvalIT</span></div>
    <div class="services">
      <span class="service-map">MapOut</span>
      <span class="service-sep"></span>
      <span class="service-ship">ShipWell</span>
      <span class="service-sep"></span>
      <span class="service-keep">KeepSteady</span>
    </div>
  </section>
</main>
</body>
</html>
```